Tidal Forge - Crypto Currency Miner Powered by Renewable Energy Website

We Need Web Pages Design for Website for Crypto Currency Miner

Serivices include:
Mining Rig Sales
Housing for Rigs turnkey on renewable energy grid
Cloud Mining term packages
Updates

http://www.vaultrigsurvey.example (Competitors sites)

Target Market(s)

Investers for Mining Rigs and terms for 1,2 or 3 years of Hash rate

Industry/Entity Type

Mining

Number of Pages Required

5+ page

Font styles to use
Sans Serif

Colors
add136
9bcb3c
606060
474747
ffc214
cadf82
fbee3e
876aae
6b449b

Requirements
Must have
• Pictures of Solar, Wind and power Factor Correction units
Nice to have
• e-commerce platform so contract terms can be purchased through website
Should not have
• Heavy construction equipment

```html
<!DOCTYPE html>
<html lang="en">
<head>
<meta charset="utf-8">
<title>Tidal Forge – Renewable Crypto Mining</title>
<link rel="stylesheet" href="https://fonts.googleapis.com/css2?family=Roboto+Condensed:wght@300;400;700&family=Roboto:wght@400;500&display=swap">
<style>
  :root{
    --green:#9bcb3c;
    --green-bright:#add136;
    --green-light:#cadf82;
    --yellow:#ffc214;
    --yellow-light:#fbee3e;
    --grey:#606060;
    --charcoal:#474747;
    --ink:#333333;
    --backdrop:#ebebeb;
    --white:#ffffff;
  }
  *{box-sizing:border-box;margin:0;padding:0}
  html,body{width:1200px;height:1200px;overflow:hidden;background:var(--backdrop)}
  body{position:relative;font-family:"Roboto Condensed",sans-serif}
  .page{position:absolute;left:322px;top:36px;width:693px;height:1455px;transform:scale(.8);transform-origin:0 0;overflow:hidden;background:var(--white);box-shadow:0 0 24px rgba(0,0,0,.08)}
  .shapes{position:absolute;left:0;top:0}
  .abs{position:absolute}
  .brand-box{left:114px;top:0;width:116px;height:122px;background:rgba(255,255,255,.82);clip-path:polygon(0 0,100% 0,100% 100%,0 88%);display:flex;flex-direction:column;align-items:center;justify-content:center;gap:8px}
  .brand-dot{width:34px;height:34px;border-radius:50%;background:var(--green)}
  .brand-name{font-family:"Roboto Condensed",sans-serif;font-weight:700;font-size:17px;color:var(--grey)}
  .nav{top:35px;left:275px;font-family:Roboto,sans-serif;font-size:8px;letter-spacing:.6px;color:var(--white);text-transform:uppercase}
  .nav span{position:absolute;white-space:nowrap}
  .hero-tag{left:121px;top:147px;width:170px;color:var(--white);font-size:11px;line-height:13px}
  .hero-title{left:117px;top:185px;color:var(--white);font-size:44px;line-height:48px;font-weight:400;letter-spacing:-1px;text-transform:uppercase;text-shadow:0 2px 3px rgba(0,0,0,.25);white-space:nowrap}
  .hero-copy{left:121px;top:339px;width:220px;color:var(--white);font-family:Roboto,sans-serif;font-size:5.6px;line-height:8px}
  .btn-dark{left:120px;top:379px;width:120px;height:27px;background:var(--ink);color:var(--white);border-radius:3px;font-size:13px;display:flex;align-items:center;justify-content:center}
  .login{left:457px;top:277px;width:111px;height:178px;background:var(--yellow);border-radius:10px;box-shadow:0 2px 6px rgba(0,0,0,.2)}
  .login-top{position:absolute;left:0;top:0;width:111px;height:45px;background:var(--yellow-light);border-radius:10px 10px 0 0}
  .avatar{position:absolute;left:20px;top:-22px;width:70px;height:70px;border-radius:50%;background:var(--green);border:5px solid var(--white);box-shadow:0 0 0 2px var(--green)}
  .field{position:absolute;left:13px;width:84px;height:16px;background:var(--white);border-radius:8px;font-family:Roboto,sans-serif;font-size:5.5px;color:#aaa;padding-left:20px;line-height:16px;letter-spacing:.4px}
  .field i{position:absolute;left:7px;top:5px;width:6px;height:6px;background:var(--ink);border-radius:1px}
  .remember{position:absolute;left:28px;top:124px;font-family:Roboto,sans-serif;font-size:4.5px;color:var(--white)}
  .remember::before{content:"";position:absolute;left:-7px;top:0;width:5px;height:5px;border-radius:50%;background:var(--ink);box-shadow:0 0 0 1px var(--white)}
  .login-btn{position:absolute;left:30px;top:140px;width:50px;height:18px;border-radius:9px;background:rgba(255,255,255,.55);color:var(--white);font-family:Roboto,sans-serif;font-size:6px;text-align:center;line-height:18px;letter-spacing:.5px}
  .register{position:absolute;left:0;top:165px;width:111px;text-align:center;font-family:Roboto,sans-serif;font-size:4px;color:var(--grey)}
  .register b{color:var(--ink)}
  .feature{top:485px;width:160px;text-align:center;color:var(--grey)}
  .feature svg{display:block;margin:0 auto}
  .feature h3{margin-top:21px;font-size:15px;line-height:18px;font-weight:300;text-transform:uppercase}
  .feature p{margin:21px auto 0;width:112px;font-family:Roboto,sans-serif;font-size:6.4px;line-height:9.2px;color:var(--ink)}
  .btn-outline{display:inline-block;margin-top:14px;width:72px;height:17px;border:1px solid;border-radius:2px;font-family:Roboto,sans-serif;font-size:7.5px;line-height:15px;text-align:center}
  .divider{top:482px;width:1px;height:215px;background:#bdbdbd}
  .buy-title{left:105px;top:833px;color:var(--white);font-size:26px;line-height:29px;font-weight:400;letter-spacing:-.4px;white-space:nowrap}
  .buy-rule{left:105px;top:898px;width:152px;height:4px;background:var(--ink)}
  .lead{font-size:11px;line-height:13px;color:var(--white);text-align:justify}
  .fine{font-size:6.3px;line-height:9.4px;color:var(--white);text-align:justify}
  .device{left:352px;top:750px;width:314px;height:352px;background:linear-gradient(160deg,#7fb8ec 0%,#3d7fd0 45%,#1f5fb0 70%,#e9f1fa 100%);border:11px solid #1d1d1d;border-radius:14px;transform:rotate(5deg)}
  .why-title{left:381px;top:1164px;color:var(--white);font-size:21px;font-weight:400;letter-spacing:-.5px;white-space:nowrap}
  .why-title em{font-style:normal;color:var(--green)}
  .tile{width:95px;height:95px;border-radius:4px;display:flex;flex-direction:column;align-items:center;justify-content:flex-end;padding-bottom:10px;gap:12px;font-size:14px;line-height:15px;text-align:center}
  .tile svg{display:block}
</style>
</head>
<body>
<div class="page">
  <svg class="shapes" width="693" height="1455" viewBox="0 0 693 1455">
    <defs>
      <linearGradient id="heroFill" x1="0" y1="0" x2="1" y2="1">
        <stop offset="0" stop-color="#7fc23a"/>
        <stop offset=".5" stop-color="#9bcb3c"/>
        <stop offset="1" stop-color="#b5d65a"/>
      </linearGradient>
    </defs>
    <g role="img" aria-label="Wind turbines in a green field under a bright sky, tinted green">
      <polygon points="0,0 693,0 693,350 0,480" fill="url(#heroFill)"/>
    </g>
    <polygon points="380,0 693,0 693,38" fill="var(--yellow)"/>
    <polygon points="470,392 693,350 693,376" fill="var(--yellow)"/>
    <polygon points="0,830 693,717 693,1070 0,1180" fill="var(--green)"/>
    <polygon points="0,1180 693,1070 693,1455 0,1455" fill="var(--charcoal)"/>
    <polygon points="480,1455 693,1420 693,1455" fill="var(--white)"/>
  </svg>

  <div class="abs brand-box"><span class="brand-dot"></span><span class="brand-name">Tidal Forge</span></div>

  <nav class="abs nav">
    <span style="left:0">Home</span>
    <span style="left:47px">Pricing</span>
    <span style="left:109px">Our Offer</span>
    <span style="left:171px">About Us</span>
    <span style="left:234px">Customer Service</span>
  </nav>

  <p class="abs hero-tag">Join over 1.000.000 people with the world's leading hashpower provider</p>
  <h1 class="abs hero-title">Start<br>Tidal Forge<br>Today!</h1>
  <p class="abs hero-copy">It's super simple - Your mining rigs are already set up and running. As soon as you've set up your account you can start to earn your first coins from our bitcoin cloud mining service!</p>
  <div class="abs btn-dark">Learn More</div>

  <form class="abs login">
    <div class="login-top"></div>
    <div class="avatar"></div>
    <div class="field" style="top:70px"><i></i>USERNAME</div>
    <div class="field" style="top:96px"><i></i>PASSWORD</div>
    <span class="remember">Remember Me !</span>
    <div class="login-btn">LOG IN</div>
    <p class="register">Don't have a account? <b>REGISTER HERE</b></p>
  </form>

  <section>
    <div class="abs feature" style="left:100px">
      <svg width="90" height="98" viewBox="0 0 90 98"><polygon points="45,3 86,26 86,72 45,95 4,72 4,26" fill="var(--yellow)" stroke="var(--yellow)" stroke-width="4" stroke-linejoin="round"/><polygon points="45,11 79,30 79,68 45,87 11,68 11,30" fill="var(--yellow)" stroke="var(--white)" stroke-width="2"/><circle cx="45" cy="49" r="18" fill="none" stroke="var(--white)" stroke-width="1.5" stroke-dasharray="6 4"/><path d="M45 49 L45 35 M45 49 L57 56 M45 49 L33 56" stroke="var(--white)" stroke-width="2.5" stroke-linecap="round"/></svg>
      <h3>Wind Power<br>Investment</h3>
      <p>Don't wrestle with rig assembly and hot, noisy miners at home. We have the fastest bitcoin mining hardware running for you already!</p>
      <span class="btn-outline" style="color:var(--grey);border-color:var(--yellow)">Learn More</span>
    </div>
    <div class="abs divider" style="left:259px"></div>
    <div class="abs feature" style="left:267px">
      <svg width="90" height="98" viewBox="0 0 90 98"><polygon points="45,3 86,26 86,72 45,95 4,72 4,26" fill="var(--green)" stroke="var(--green)" stroke-width="4" stroke-linejoin="round"/><polygon points="45,11 79,30 79,68 45,87 11,68 11,30" fill="var(--green)" stroke="var(--white)" stroke-width="2"/><rect x="28" y="42" width="34" height="20" fill="none" stroke="var(--white)" stroke-width="1.5"/><path d="M28 49h34M28 55h34M39 42v20M51 42v20M45 62v6M38 68h14" stroke="var(--white)" stroke-width="1.2"/><circle cx="45" cy="33" r="3" fill="none" stroke="var(--white)" stroke-width="1.2"/></svg>
      <h3>Solar Power<br>Investment</h3>
      <p>Don't wrestle with rig assembly and hot, noisy miners at home. We have the fastest bitcoin mining hardware running for you already!</p>
      <span class="btn-outline" style="color:var(--ink);border-color:var(--green)">Learn More</span>
    </div>
    <div class="abs divider" style="left:430px"></div>
    <div class="abs feature" style="left:437px">
      <svg width="90" height="98" viewBox="0 0 90 98"><polygon points="45,3 86,26 86,72 45,95 4,72 4,26" fill="var(--charcoal)" stroke="var(--charcoal)" stroke-width="4" stroke-linejoin="round"/><polygon points="45,11 79,30 79,68 45,87 11,68 11,30" fill="var(--charcoal)" stroke="var(--white)" stroke-width="2"/><rect x="27" y="42" width="36" height="24" rx="3" fill="none" stroke="var(--white)" stroke-width="1.8"/><rect x="50" y="49" width="13" height="9" rx="2" fill="none" stroke="var(--white)" stroke-width="1.5"/><path d="M32 42 L46 32 L56 42" fill="none" stroke="var(--white)" stroke-width="1.5"/></svg>
      <h3>Get Your First<br>Payout Today</h3>
      <p>Don't wrestle with rig assembly and hot, noisy miners at home. We have the fastest bitcoin mining hardware running for you already!</p>
      <span class="btn-outline" style="color:var(--ink);border-color:var(--charcoal)">Learn More</span>
    </div>
  </section>

  <section>
    <h2 class="abs buy-title">Buy And Sell<br>Crypto Currency Miner</h2>
    <div class="abs buy-rule"></div>
    <p class="abs lead" style="left:112px;top:915px;width:200px">Lorem ipsum dolor sit amet, consectetur adipisicing elit. Aliquam praesentium, distinctio dicta molestias dignissimos.</p>
    <p class="abs fine" style="left:112px;top:965px;width:200px">Lorem ipsum dolor sit amet, consectetur adipisicing elit. Quam earum, provident ad, porro aperiam dolore, blanditiis, nihil pariatur eius adipisci consequuntur officiis. Excepturi, nostrum? Id incidunt nesciunt officia hic distinctio nihil pariatur.</p>
    <p class="abs fine" style="left:112px;top:1012px;width:200px">Lorem ipsum dolor sit amet, consectetur adipisicing elit. Quam earum, provident ad, porro aperiam dolore, blanditiis, nihil pariatur eius adipisci consequuntur officiis. Excepturi, nostrum? Id incidunt nesciunt officia hic distinctio nihil pariatur. Lorem ipsum dolor sit amet, consectetur adipisicing elit. Quam earum, provident ad, porro aperiam dolore, blanditiis, nihil pariatur eius adipisci consequuntur officiis. Excepturi, nostrum? Id incidunt nesciunt officia hic distinctio nihil pariatur.</p>
    <span class="abs btn-outline" style="left:239px;top:1075px;color:var(--white);border-color:var(--white)">Learn More</span>
    <div class="abs device" role="img" aria-label="Tablet showing a green planet ringed with solar panels, wind turbines and clouds"></div>
  </section>

  <section>
    <h2 class="abs why-title">Why Choose <em>Tidal Forge</em>?</h2>
    <div class="abs" style="left:381px;top:1197px;width:100px;height:1px;background:#8a8a8a"></div>
    <div class="abs" style="left:481px;top:1195px;width:101px;height:4px;background:var(--green)"></div>
    <p class="abs lead" style="left:388px;top:1212px;width:200px">Lorem ipsum dolor sit amet, consectetur adipisicing elit. Aliquam praesentium, distinctio dicta molestias dignissimos.</p>
    <p class="abs fine" style="left:388px;top:1262px;width:200px">Lorem ipsum dolor sit amet, consectetur adipisicing elit. Quam earum, provident ad, porro aperiam dolore, blanditiis, nihil pariatur eius adipisci consequuntur officiis. Excepturi, nostrum? Id incidunt nesciunt officia hic distinctio nihil pariatur.</p>
    <p class="abs fine" style="left:388px;top:1309px;width:200px">Lorem ipsum dolor sit amet, consectetur adipisicing elit. Quam earum, provident ad, porro aperiam dolore, blanditiis, nihil pariatur eius adipisci consequuntur officiis. Excepturi, nostrum? Id incidunt nesciunt officia hic distinctio nihil pariatur. Lorem ipsum dolor sit amet, consectetur adipisicing elit. Quam earum, provident ad, porro aperiam dolore, blanditiis, nihil pariatur eius adipisci consequuntur officiis. Excepturi, nostrum? Id incidunt nesciunt officia hic distinctio nihil pariatur.</p>
    <span class="abs btn-outline" style="left:515px;top:1373px;color:var(--white);border-color:var(--white)">Learn More</span>

    <div class="abs tile" style="left:120px;top:1208px;background:var(--green);color:var(--white)">
      <svg width="40" height="48" viewBox="0 0 40 48"><path d="M20 3 L36 9 V24 C36 35 28 42 20 45 C12 42 4 35 4 24 V9 Z" fill="none" stroke="var(--white)" stroke-width="2"/><circle cx="20" cy="21" r="5" fill="none" stroke="var(--white)" stroke-width="2"/><path d="M20 26v8" stroke="var(--white)" stroke-width="2.5"/></svg>
      <span>Safe And Secure</span>
    </div>
    <div class="abs tile" style="left:239px;top:1208px;background:var(--yellow);color:var(--white)">
      <svg width="44" height="48" viewBox="0 0 44 48"><rect x="6" y="4" width="22" height="40" rx="3" fill="none" stroke="var(--white)" stroke-width="2"/><circle cx="30" cy="22" r="7" fill="none" stroke="var(--white)" stroke-width="2" stroke-dasharray="3 2"/><circle cx="30" cy="22" r="2.5" fill="var(--white)"/><circle cx="15" cy="18" r="5" fill="none" stroke="var(--white)" stroke-width="2" stroke-dasharray="3 2"/></svg>
      <span>Mobile App</span>
    </div>
    <div class="abs tile" style="left:120px;top:1321px;background:var(--yellow-light);color:var(--ink)">
      <svg width="46" height="44" viewBox="0 0 46 44"><rect x="6" y="8" width="34" height="26" rx="3" fill="none" stroke="var(--ink)" stroke-width="2"/><path d="M6 16h34" stroke="var(--ink)" stroke-width="2"/><rect x="30" y="20" width="12" height="8" rx="2" fill="none" stroke="var(--ink)" stroke-width="2"/><path d="M12 24 L16 28 L22 20" fill="none" stroke="var(--ink)" stroke-width="2"/></svg>
      <span>Secure Wallet</span>
    </div>
    <div class="abs tile" style="left:239px;top:1321px;background:var(--white);color:var(--ink)">
      <svg width="44" height="46" viewBox="0 0 44 46"><rect x="6" y="6" width="26" height="34" rx="2" fill="none" stroke="var(--ink)" stroke-width="2"/><path d="M19 14 L27 17 V24 C27 29 23 32 19 33 C15 32 11 29 11 24 V17 Z" fill="none" stroke="var(--ink)" stroke-width="1.8"/><circle cx="34" cy="34" r="7" fill="var(--white)" stroke="var(--ink)" stroke-width="2"/><path d="M34 30v8M30 34h8" stroke="var(--ink)" stroke-width="2"/></svg>
      <span>Covered By<br>Insurance</span>
    </div>
  </section>
</div>
</body>
</html>
```